Web Design

We need a website for a company based in Doha Qatar called
Lumara Maid Service.

It is the number one maid cleaning service company, and we have branches all over qatar.

Luxury Cleaning Service Provider.

The color scheme is gold, yellow and black like the logo.

Before they get to the website, there is an intro video.

The website should depict luxury.

Target Market(s)

People who need maids at their houses.

Industry/Entity Type

Cleaning Service

Requirements
Must have
• Luxury, Sleek, Modern

The opening sequence is a video which I already have. Its too big to upload here so I am going to put it on youtube.

After the opening sequence, the home page should have a widescreen photo background and it should change every five seconds, the first background photo should be of qatar westbay skyline. Then the second background should be of maid photos in cleaning positions. Then the third background should be of cleaner photos etc.

We will send you all the tabs and all the content later.

```html
<!DOCTYPE html>
<html lang="en">
<head>
<meta charset="utf-8">
<title>Lumara Maid Service</title>
<link href="https://fonts.googleapis.com/css2?family=Open+Sans:wght@400;600&display=swap" rel="stylesheet">
<style>
:root{
  --brown:#5a2608;
  --brown-dark:#6b2a05;
  --accent:#dc4b1c;
  --gold:#e0a030;
  --text:#595959;
  --line:#dcdcdc;
  --panel:#f1f1f1;
  --hero:#e4e4e8;
}
*{margin:0;padding:0;box-sizing:border-box}
html,body{width:932px;height:1200px;overflow:hidden;background:#fff}
body{font-family:"Open Sans",Arial,sans-serif;color:var(--text);position:relative}
.abs{position:absolute}
.brand{left:79px;top:40px;display:flex;align-items:center;gap:10px;font-size:20px;font-weight:600;color:var(--brown)}
.brand-dot{width:26px;height:26px;border-radius:50%;background:var(--gold)}
.search{left:733px;top:28px;width:121px;height:25px;border:1px solid #d6d6d6;border-radius:3px;font-size:10.5px;color:#999;padding:5px 0 0 19px}
.search svg{position:absolute;right:4px;top:4px}
.search .sep{position:absolute;right:24px;top:4px;width:1px;height:15px;background:#ddd}
.nav{top:83px;left:494px;display:flex;font-size:11.5px;color:#666}
.nav a{text-decoration:none;color:inherit;margin-right:26.5px}
.nav a:last-child{margin-right:0}
.nav a.active{color:var(--accent)}
.hero{left:0;top:126px;width:932px;height:376px;background:var(--hero)}
.hero-photo{left:559px;top:126px;width:373px;height:376px;background:linear-gradient(90deg,#e9e8ea,#f4f3f2 40%,#ecebea)}
.hero-title{left:100px;top:263px;font-size:22px;color:#3c3c3c}
.hero-btn{left:100px;top:300px;width:83px;height:28px;background:var(--brown-dark);border-radius:3px;color:#fff;font-size:12px;text-align:center;line-height:28px}
.arrow{top:290px;width:37px;height:49px;background:#7d7d7d}
.arrow svg{display:block;margin:9px auto 0}
.service{top:527px;width:245px}
.service .pic{height:121px}
.service h3{margin-top:10px;text-align:center;font-weight:400;font-size:15.5px;color:var(--accent)}
.rule{height:1px;background:var(--line)}
h2{font-weight:400;font-size:17px;color:var(--brown)}
.copy{font-size:10.5px;line-height:17.8px}
.copy p{margin-top:9px}
.list{display:grid;grid-template-columns:261px 230px;row-gap:4px;list-style:none;margin-top:10px;font-size:12px;color:var(--accent)}
.list li::before{content:"•";font-size:8px;margin-right:7px;vertical-align:2px}
.quick{left:647px;top:733px;width:207px;height:367px;background:var(--panel)}
.quick-head{height:35px;background:linear-gradient(#6e2c05,#5a2304);color:#fff;font-size:15.5px;padding:5px 8px}
.field{position:absolute;left:22px;width:163px;height:29px;background:#fff;border:1px solid #dadada;border-radius:2px;font-size:10px;color:#888;padding:7px 11px}
.submit{position:absolute;left:120px;top:323px;width:65px;height:28px;border-radius:3px;background:linear-gradient(#f6b33a,#e79a1e);color:#4a2006;font-size:12px;text-align:center;line-height:28px}
.footer{left:0;top:1129px;width:932px;height:71px;background:#f0f0f0}
.footer-links{left:79px;top:1145px;font-size:9.5px;color:#555;word-spacing:2px}
.footer-links span{margin:0 7px;color:#999}
.copyright{left:79px;top:1167px;font-size:9.5px;color:#555}
.social{top:1152px;width:24px;height:24px;border-radius:50%}
</style>
</head>
<body>
<header>
  <div class="abs brand"><span class="brand-dot"></span>Lumara Maid Service</div>
  <div class="abs search">Search<span class="sep"></span>
    <svg width="14" height="14" viewBox="0 0 14 14"><circle cx="5.5" cy="5.5" r="4.2" fill="none" stroke="#888" stroke-width="1.8"/><line x1="8.6" y1="8.6" x2="13" y2="13" stroke="#888" stroke-width="2"/></svg>
  </div>
  <nav class="abs nav"><a class="active">HOME</a><a>ABOUT US</a><a>SERVICES</a><a>GALLERY</a><a>CONTACT US</a></nav>
</header>

<section>
  <div class="abs hero"></div>
  <div class="abs hero-photo" role="img" aria-label="Smiling maid holding a stack of folded white towels in a bright room"></div>
  <div class="abs hero-title">Aenean tempor ligula feugiat...</div>
  <div class="abs hero-btn">Contact us</div>
  <div class="abs arrow" style="left:0"><svg width="16" height="30" viewBox="0 0 16 30"><polyline points="14,1 2,15 14,29" fill="none" stroke="#fff" stroke-width="1.5"/></svg></div>
  <div class="abs arrow" style="left:895px"><svg width="16" height="30" viewBox="0 0 16 30"><polyline points="2,1 14,15 2,29" fill="none" stroke="#fff" stroke-width="1.5"/></svg></div>
</section>

<section>
  <div class="abs service" style="left:79px"><div class="pic" role="img" aria-label="Maid cleaning an office desk" style="background:linear-gradient(135deg,#dfe4ec,#a9b6c9 60%,#e6e9ee)"></div><h3>Commercial Cleaning Service</h3></div>
  <div class="abs service" style="left:344px"><div class="pic" role="img" aria-label="Cleaners wiping cabinets in a home" style="background:linear-gradient(90deg,#b8642e,#d9a27a 45%,#c8c4c0 70%,#6f7b8f)"></div><h3>Residential Cleaning Service</h3></div>
  <div class="abs service" style="left:609px"><div class="pic" role="img" aria-label="Maid ironing colourful laundry" style="background:linear-gradient(180deg,#d8dbe4,#c5cad8 55%,#e8c23a 75%,#d8d8d8)"></div><h3>Support Service</h3></div>
  <div class="abs rule" style="left:79px;top:705px;width:775px"></div>
</section>

<main>
  <div class="abs" style="left:79px;top:727px;width:530px">
    <h2>Welcome to Lumara Maid Service</h2>
    <div class="copy"><p>Praesent at mi nunc. Nulla velit lorem, facilisis ut hendrerit nec, placerat nec metus. Suspendisse auctor, velit ut ultricies rhoncus, sem purus mattis nunc, at lobortis neque nisi eu tellus. In pretium vulputate nisi, ut pellentesque leo. Pellentesque quis mauris ante. Aenean bibendum libero mi, quis pulvinar ipsum bibendum porttitor. Donec eros nulla, varius id faucibus vitae, ullamcorper vitae nisi. Donec nisl risus, ultrices luctus elit volutpat, dapibus tincidunt libero. Phasellus hendrerit sit amet mauris eget molestie. Curabitur neque nulla, consequat sit amet ullamcorper ut, auctor placerat magna. Vestibulum at tincidunt risus. Ut eget enim varius magna congue porta id nec nibh.</p></div>
  </div>
  <div class="abs rule" style="left:79px;top:908px;width:530px"></div>
  <div class="abs" style="left:79px;top:924px;width:530px">
    <h2>Why us?</h2>
    <div class="copy"><p>Curabitur id est pulvinar, imperdiet justo ac, vehicula turpis. Donec arcu risus, vehicula sed hendrerit non, elementum sodales lectus. Integer vel ante turpis. Pellentesque ligula arcu, elementum quis enim vel, lobortis lacinia sapien.</p></div>
    <ul class="list">
      <li>Fusce non tincidunt lorem</li><li>Nunc consequat sagittis mauris in</li>
      <li>Vivamus eleifend nibh sed felis volutpat</li><li>Praesent tincidunt ipsum</li>
      <li>Pellentesque habitant morbi</li><li>Sed ullamcorper iaculis est aliquet aliquet</li>
    </ul>
  </div>

  <aside class="abs quick">
    <div class="quick-head">Quick Contact</div>
    <div class="field" style="top:59px">Name</div>
    <div class="field" style="top:99px">Phone</div>
    <div class="field" style="top:140px">E-mail</div>
    <div class="field" style="top:180px">Service For
      <svg style="position:absolute;right:10px;top:11px" width="11" height="6" viewBox="0 0 11 6"><polygon points="0,0 11,0 5.5,6" fill="#555"/></svg></div>
    <div class="field" style="top:221px;height:86px">Message</div>
    <div class="submit">SUBMIT</div>
  </aside>
</main>

<footer>
  <div class="abs footer"></div>
  <div class="abs footer-links">Home<span>|</span>About us<span>|</span>Service<span>|</span>Gallery<span>|</span>Contact us</div>
  <div class="abs copyright">Copyright &copy; 2014 Lumara Maid Service. &nbsp;All rights reserved.</div>
  <div class="abs social" style="left:795px;background:#2f4f92"></div>
  <div class="abs social" style="left:831px;background:#2da4e0"></div>
</footer>
</body>
</html>
```